Create a Big Data Website that is professional but has a creative flare to it.

I am after a modern business design for a company in the Big Data space however it still needs to have a wow value and something stand out from other corporate websites.
My competitors websites are to give you and idea of content:
www.tarnvilla.com
www.pluvoria.com
www.meridu4.com.au
www.quornaby.com
I have uploaded my company Logo so you can use that to make sure it matches your theme.

Target Market(s)

Banks, Insurance Companies, Government, Gas and Energy Companies and Food Manufacturing.

Industry/Entity Type

Consulting

Coding

Number of Pages Required

5+ page

Colors

Designer to choose colors to be used in the design.

Requirements
Must have
• Images, Diagrams around Big Data. Usage of information or graphs from sources like Velsham are fine to use.
Nice to have
• Interactive design use mouse overs, change in text, highlighting information for clear focus.
Should not have
• Cluttered Pages of Informaiton

```html
<!DOCTYPE html>
<html lang="en">
<head>
<meta charset="utf-8">
<title>Quantara Consulting</title>
<link rel="stylesheet" href="https://fonts.googleapis.com/css2?family=Roboto:wght@400;500;700;900&family=Open+Sans:ital,wght@0,400;0,600;0,700;1,400&display=swap">
<style>
:root{
  --blue:#1d8fd8;
  --blue-dark:#0e5fa8;
  --navy:#0c2f63;
  --ink:#1b1b1b;
  --muted:#7a7a7a;
  --line:#d9dde3;
  --soft:#f1f4f8;
  --star:#f4c315;
  --white:#fff;
}
*{box-sizing:border-box;margin:0;padding:0}
html,body{width:1200px;height:3586px;overflow:hidden;background:var(--white)}
body{position:relative;font-family:"Open Sans",Arial,sans-serif;color:var(--ink)}
.abs{position:absolute}
h2.section-title{position:absolute;left:0;width:1200px;text-align:center;font-family:"Roboto",Arial,sans-serif;font-weight:700;font-size:29px;letter-spacing:.3px;color:var(--ink)}

/* hero */
.hero{left:0;top:0;width:1200px;height:543px;clip-path:polygon(0 0,1200px 0,1200px 406px,968px 543px,232px 543px,0 406px);
  background:radial-gradient(ellipse at 45% 70%,#4f8fd0 0%,#21589a 35%,#0b2a5c 70%,#061838 100%)}
.hero-glow{left:0;top:0;width:1200px;height:543px;background:linear-gradient(180deg,rgba(5,20,50,.55) 0%,rgba(5,20,50,0) 22%)}
.brand{left:98px;top:36px;display:flex;align-items:center;gap:10px;color:var(--white)}
.brand-mark{width:40px;height:40px;border:3px solid var(--white);border-radius:50%}
.brand-name{font-family:"Roboto",sans-serif;font-weight:700;font-size:34px;line-height:1}
.brand-sub{font-size:9px;letter-spacing:1.6px;text-transform:uppercase;margin-top:3px}
.nav{right:98px;top:48px;display:flex;gap:32px;font-family:"Roboto",sans-serif;font-weight:500;font-size:14px;color:var(--white)}
.nav .active{color:var(--blue)}
.hero-title{left:0;top:182px;width:1200px;text-align:center;font-family:"Roboto",sans-serif;font-weight:700;font-size:58px;color:var(--white);letter-spacing:.5px}
.hero-sub{left:0;top:257px;width:1200px;text-align:center;font-size:21px;font-weight:600;color:var(--white)}
.btn-hero{left:502px;top:308px;width:196px;height:47px;border-radius:24px;background:var(--blue);color:var(--white);font-family:"Roboto",sans-serif;font-weight:700;font-size:14px;display:flex;align-items:center;justify-content:center}
.dots{left:570px;top:474px;display:flex;gap:6px}
.dots i{width:10px;height:10px;border-radius:50%;border:1.5px solid var(--white)}
.dots i.on{background:var(--white)}

/* welcome */
.lead{left:170px;top:694px;width:860px;text-align:center;font-size:13.5px;line-height:26px;color:var(--muted)}
.feature{width:330px;height:100px}
.feature svg{position:absolute;left:0;top:0}
.feature h3{position:absolute;left:108px;top:6px;font-family:"Roboto",sans-serif;font-weight:500;font-size:19px;color:var(--ink)}
.feature p{position:absolute;left:108px;top:36px;width:210px;font-size:13px;line-height:22px;color:var(--muted)}

/* why */
.why{left:0;top:1107px;width:1200px;height:466px;background:var(--soft)}
.why h2{position:absolute;left:96px;top:86px;font-family:"Roboto",sans-serif;font-weight:700;font-size:30px}
.why ul{position:absolute;left:96px;top:150px;list-style:none}
.why li{display:flex;align-items:center;gap:14px;height:29px;font-size:13px;color:#555}
.why li svg{flex:none}
.btn-outline{position:absolute;left:98px;top:355px;width:138px;height:38px;border:1.5px solid var(--blue);border-radius:20px;color:var(--blue-dark);font-family:"Roboto",sans-serif;font-weight:700;font-size:13px;display:flex;align-items:center;justify-content:center}
.device-photo{position:absolute;left:566px;top:56px;width:538px;height:354px;border-radius:8px;
  background:linear-gradient(180deg,#3a3d42 0%,#3a3d42 3%,#eef1f5 3%,#dfe5ee 60%,#b9c0c9 92%,#8f969f 100%)}

/* blog */
.post{width:322px}
.post-media{position:relative;width:322px;height:210px}
.date{position:absolute;left:0;top:140px;width:42px;height:64px;background:var(--blue);color:var(--white);text-align:center;font-family:"Roboto",sans-serif}
.date b{display:block;font-size:22px;margin-top:8px}
.date span{font-size:12px}
.post h3{margin-top:38px;font-family:"Roboto",sans-serif;font-weight:500;font-size:17px;line-height:23px}
.post p{margin-top:14px;font-size:12.5px;line-height:20px;color:var(--muted)}
.author{margin-top:22px;display:flex;align-items:center;gap:7px;font-size:11.5px;color:#555}

/* testimonials */
.testimonials{left:0;top:2194px;width:1200px;height:376px;background:linear-gradient(180deg,#2497dc 0%,#1585d0 100%)}
.testimonials h2{color:var(--white);top:76px}
.quote{position:absolute;width:320px;height:190px}
.avatar{position:absolute;left:0;top:0;width:72px;height:72px;border-radius:50%;border:3px solid var(--white);background:radial-gradient(circle at 50% 40%,#c9c2bb,#7b7470)}
.quote p{position:absolute;left:98px;top:2px;width:222px;font-style:italic;font-size:11.5px;line-height:19px;color:var(--white)}
.quote p::before{content:"“";font-size:30px;font-weight:700;position:absolute;left:-16px;top:-6px;font-style:normal}
.quote .who{position:absolute;left:98px;top:82px;font-size:10px;font-weight:700;color:var(--white);text-transform:uppercase;letter-spacing:.4px}
.quote .role{position:absolute;left:98px;top:98px;font-size:10px;font-style:italic;color:#d8ecfa}
.quote .stars{position:absolute;left:98px;top:142px;display:flex;gap:5px}
.arrow{position:absolute;top:150px;width:36px;height:36px;border-radius:50%;background:rgba(255,255,255,.25);display:flex;align-items:center;justify-content:center}

/* partners */
.partner{width:184px;height:78px;border:1px solid var(--line);display:flex;align-items:center;justify-content:center;font-family:"Roboto",sans-serif;font-weight:700;font-size:17px;color:#5b5f66}

/* contact */
.contact{left:0;top:3024px;width:1200px;height:562px;clip-path:polygon(240px 0,960px 0,1200px 131px,1200px 562px,0 562px,0 131px);
  background:radial-gradient(ellipse at 70% 40%,#1a4f93 0%,#0e3672 50%,#0a2756 100%)}
.contact h2{color:var(--white);top:70px}
.contact h4{position:absolute;font-family:"Roboto",sans-serif;font-weight:500;font-size:19px;color:var(--white)}
.field{position:absolute;height:34px;border:1px solid rgba(255,255,255,.55);font-size:11px;color:var(--white);padding:9px 12px}
.submit{position:absolute;left:628px;top:414px;width:100px;height:34px;border-radius:18px;background:var(--blue);color:var(--white);font-family:"Roboto",sans-serif;font-weight:700;font-size:13px;display:flex;align-items:center;justify-content:center}
.info{position:absolute;left:782px;display:flex;gap:18px;font-size:12px;line-height:20px;color:var(--white)}
.info .ico{width:36px;height:36px;border-radius:50%;border:1px solid rgba(255,255,255,.55);display:flex;align-items:center;justify-content:center;flex:none}
.social{position:absolute;left:782px;top:408px;display:flex;gap:8px}
.social span{height:28px;padding:0 10px;border-radius:14px;background:#2a78c8;color:var(--white);font-size:11px;font-weight:600;display:flex;align-items:center}
.footer-rule{position:absolute;left:96px;top:478px;width:1008px;height:1px;background:rgba(255,255,255,.3)}
.copyright{position:absolute;left:0;top:512px;width:1200px;text-align:center;font-size:11px;color:#cfd9e8}
.to-top{position:absolute;left:1072px;top:498px}
</style>
</head>
<body>

<!-- hero -->
<div class="abs hero" role="img" aria-label="Photo of a hand holding a glowing blue data chart with rising line graphs"></div>
<div class="abs hero-glow"></div>
<div class="abs brand">
  <div class="brand-mark"></div>
  <div><div class="brand-name">quantara</div><div class="brand-sub">Consulting Services</div></div>
</div>
<nav class="abs nav"><span class="active">HOME</span><span>ABOUT</span><span>SOLUTIONS</span><span>PARTNERS</span><span>BLOG</span><span>CONTACT US</span>
  <svg width="16" height="16" viewBox="0 0 16 16"><circle cx="6.5" cy="6.5" r="4.5" fill="none" stroke="#fff" stroke-width="2"/><line x1="10" y1="10" x2="14.5" y2="14.5" stroke="#fff" stroke-width="2"/></svg>
</nav>
<h1 class="abs hero-title">QUANTARA CONSULTING</h1>
<div class="abs hero-sub">We provide services related to Big Data</div>
<div class="abs btn-hero">GET MORE INFO</div>
<div class="abs dots"><i class="on"></i><i></i><i></i><i></i></div>

<!-- welcome -->
<h2 class="section-title" style="top:634px">WELCOME TO QUANTARA CONSULTING</h2>
<p class="abs lead">At vero eos et accusamus et iusto odio dignissimos ducimus qui blanditiis praesentium voluptatum deleniti atque corrupti quos dolores et quas molestias excepturi sint occaecati cupiditate non provident, optio cumque nihil impedit quo</p>

<div class="abs feature" style="left:96px;top:796px">
  <svg width="92" height="92" viewBox="0 0 92 92"><polygon points="46,4 84,25 84,67 46,88 8,67 8,25" fill="none" stroke="#1d8fd8" stroke-width="2.5"/><path d="M30 60 V42 l8 8 8-12 8 8 8-6 V60 Z" fill="#0e5fa8"/></svg>
  <h3>Data Visualisation</h3><p>Nam libero tempore, cum soluta nobis est eligendi optio.</p>
</div>
<div class="abs feature" style="left:447px;top:796px">
  <svg width="92" height="92" viewBox="0 0 92 92"><polygon points="46,4 84,25 84,67 46,88 8,67 8,25" fill="none" stroke="#1d8fd8" stroke-width="2.5"/><circle cx="46" cy="40" r="11" fill="none" stroke="#0e5fa8" stroke-width="3"/><rect x="40" y="52" width="12" height="8" fill="#0e5fa8"/></svg>
  <h3>Business Intelligence</h3><p>Nam libero tempore, cum soluta nobis est eligendi optio.</p>
</div>
<div class="abs feature" style="left:798px;top:796px">
  <svg width="92" height="92" viewBox="0 0 92 92"><polygon points="46,4 84,25 84,67 46,88 8,67 8,25" fill="none" stroke="#1d8fd8" stroke-width="2.5"/><rect x="30" y="30" width="32" height="30" fill="none" stroke="#0e5fa8" stroke-width="2.5"/><rect x="35" y="46" width="4" height="10" fill="#0e5fa8"/><rect x="42" y="40" width="4" height="16" fill="#0e5fa8"/><rect x="49" y="36" width="4" height="20" fill="#0e5fa8"/><rect x="56" y="43" width="3" height="13" fill="#0e5fa8"/></svg>
  <h3>Advanced Analytics</h3><p>Nam libero tempore, cum soluta nobis est eligendi optio.</p>
</div>
<div class="abs feature" style="left:96px;top:930px">
  <svg width="92" height="92" viewBox="0 0 92 92"><polygon points="46,4 84,25 84,67 46,88 8,67 8,25" fill="none" stroke="#1d8fd8" stroke-width="2.5"/><rect x="28" y="36" width="36" height="22" rx="2" fill="none" stroke="#0e5fa8" stroke-width="3"/><circle cx="46" cy="47" r="6" fill="#0e5fa8"/></svg>
  <h3>Data Enrichment</h3><p>Nam libero tempore, cum soluta nobis est eligendi optio.</p>
</div>
<div class="abs feature" style="left:447px;top:930px">
  <svg width="92" height="92" viewBox="0 0 92 92"><polygon points="46,4 84,25 84,67 46,88 8,67 8,25" fill="none" stroke="#1d8fd8" stroke-width="2.5"/><path d="M30 40 H60 M54 34 l6 6 -6 6 M62 54 H32 M38 48 l-6 6 6 6" fill="none" stroke="#0e5fa8" stroke-width="3.5"/></svg>
  <h3>Data Integration</h3><p>Nam libero tempore, cum soluta nobis est eligendi optio.</p>
</div>
<div class="abs feature" style="left:798px;top:930px">
  <svg width="92" height="92" viewBox="0 0 92 92"><polygon points="46,4 84,25 84,67 46,88 8,67 8,25" fill="none" stroke="#1d8fd8" stroke-width="2.5"/><circle cx="42" cy="48" r="9" fill="none" stroke="#0e5fa8" stroke-width="5" stroke-dasharray="4 3"/><circle cx="42" cy="48" r="3" fill="#0e5fa8"/><circle cx="58" cy="36" r="5" fill="none" stroke="#0e5fa8" stroke-width="3" stroke-dasharray="3 2"/></svg>
  <h3>Automated CRM</h3><p>Nam libero tempore, cum soluta nobis est eligendi optio.</p>
</div>

<!-- why choose us -->
<section class="abs why">
  <h2>WHY CHOOSE US</h2>
  <ul>
    <li><svg width="14" height="14" viewBox="0 0 14 14"><circle cx="7" cy="7" r="7" fill="#0e5fa8"/><path d="M3.5 7 l2.5 2.5 4.5-5" fill="none" stroke="#fff" stroke-width="1.8"/></svg>At vero eos et accusamus et iusto odio dignissimos ducimus qui</li>
    <li><svg width="14" height="14" viewBox="0 0 14 14"><circle cx="7" cy="7" r="7" fill="#0e5fa8"/><path d="M3.5 7 l2.5 2.5 4.5-5" fill="none" stroke="#fff" stroke-width="1.8"/></svg>Blanditiis praesentium voluptatum deleniti atque corrupti quos dolores</li>
    <li><svg width="14" height="14" viewBox="0 0 14 14"><circle cx="7" cy="7" r="7" fill="#0e5fa8"/><path d="M3.5 7 l2.5 2.5 4.5-5" fill="none" stroke="#fff" stroke-width="1.8"/></svg>Et quas molestias excepturi sint occaecati cupiditat imilique sunt sculpa</li>
    <li><svg width="14" height="14" viewBox="0 0 14 14"><circle cx="7" cy="7" r="7" fill="#0e5fa8"/><path d="M3.5 7 l2.5 2.5 4.5-5" fill="none" stroke="#fff" stroke-width="1.8"/></svg>Qui officia deserunt mollitia animi, id est laborum et dolorum fuga</li>
    <li><svg width="14" height="14" viewBox="0 0 14 14"><circle cx="7" cy="7" r="7" fill="#0e5fa8"/><path d="M3.5 7 l2.5 2.5 4.5-5" fill="none" stroke="#fff" stroke-width="1.8"/></svg>Et harum quidem rerum facilis est et expedita distinctionnis dolor</li>
    <li><svg width="14" height="14" viewBox="0 0 14 14"><circle cx="7" cy="7" r="7" fill="#0e5fa8"/><path d="M3.5 7 l2.5 2.5 4.5-5" fill="none" stroke="#fff" stroke-width="1.8"/></svg>Repellendus autem quibusdam et aut officiis debitis aut rerum neces</li>
  </ul>
  <div class="btn-outline">READ MORE</div>
  <div class="device-photo" role="img" aria-label="Photo of an open laptop showing a data growth chart"></div>
</section>

<!-- blog -->
<h2 class="section-title" style="top:1641px">LATEST BLOG</h2>
<article class="abs post" style="left:96px;top:1721px">
  <div class="post-media" role="img" aria-label="Photo of hands working on a tablet and laptop" style="background:linear-gradient(135deg,#e9e6e1 0%,#b9b3aa 55%,#6d655d 100%)"><div class="date"><b>04</b><span>SEP</span></div></div>
  <h3>At vero eos et accusamus et iustoer odio dignissimos duci</h3>
  <p>At vero eos et accusamus et iusto odio dignissimodu cimus qui blanditiis praesentium volup</p>
  <div class="author"><svg width="11" height="11" viewBox="0 0 11 11"><circle cx="5.5" cy="3" r="2.7" fill="#0e5fa8"/><path d="M0.5 11 a5 5 0 0 1 10 0Z" fill="#0e5fa8"/></svg>Maren Holloway</div>
</article>
<article class="abs post" style="left:440px;top:1721px">
  <div class="post-media" role="img" aria-label="Illustration of a glowing digital network in deep blue" style="background:radial-gradient(ellipse at 60% 40%,#3b78b8 0%,#143a6e 55%,#081a38 100%)"><div class="date"><b>30</b><span>AUG</span></div></div>
  <h3>At vero eos et accusamus et iustoer odio dignissimos duci</h3>
  <p>At vero eos et accusamus et iusto odio dignissimodu cimus qui blanditiis praesentium volup</p>
  <div class="author"><svg width="11" height="11" viewBox="0 0 11 11"><circle cx="5.5" cy="3" r="2.7" fill="#0e5fa8"/><path d="M0.5 11 a5 5 0 0 1 10 0Z" fill="#0e5fa8"/></svg>Maren Holloway</div>
</article>
<article class="abs post" style="left:784px;top:1721px">
  <div class="post-media" role="img" aria-label="Photo of a team reviewing charts and sticky notes on a desk" style="background:linear-gradient(135deg,#d9d3c9 0%,#c9b79a 45%,#8a8f86 100%)"><div class="date"><b>08</b><span>SEP</span></div></div>
  <h3>At vero eos et accusamus et iustoer odio dignissimos duci</h3>
  <p>At vero eos et accusamus et iusto odio dignissimodu cimus qui blanditiis praesentium volup</p>
  <div class="author"><svg width="11" height="11" viewBox="0 0 11 11"><circle cx="5.5" cy="3" r="2.7" fill="#0e5fa8"/><path d="M0.5 11 a5 5 0 0 1 10 0Z" fill="#0e5fa8"/></svg>Maren Holloway</div>
</article>

<!-- testimonials -->
<section class="abs testimonials">
  <h2 class="section-title">CLIENT TESTIMONIALS</h2>
  <div class="arrow" style="left:28px"><svg width="12" height="12" viewBox="0 0 12 12"><path d="M8 1 L3 6 L8 11" fill="none" stroke="#fff" stroke-width="2"/></svg></div>
  <div class="arrow" style="left:1136px"><svg width="12" height="12" viewBox="0 0 12 12"><path d="M4 1 L9 6 L4 11" fill="none" stroke="#fff" stroke-width="2"/></svg></div>

  <div class="quote" style="left:96px;top:138px">
    <div class="avatar" role="img" aria-label="Client portrait"></div>
    <p>At vero eos et accusamus et iustodio dignissimos ducimus qui blanditiipraesent ium voluptatum deleniti atqu.</p>
    <div class="who">Delia Morrow</div><div class="role">Financial Services Professional</div>
    <div class="stars"><svg width="100" height="16" viewBox="0 0 100 16"><g fill="#f4c315"><polygon points="8,0 10,5.5 16,6 11.5,10 13,16 8,12.7 3,16 4.5,10 0,6 6,5.5"/><polygon transform="translate(21 0)" points="8,0 10,5.5 16,6 11.5,10 13,16 8,12.7 3,16 4.5,10 0,6 6,5.5"/><polygon transform="translate(42 0)" points="8,0 10,5.5 16,6 11.5,10 13,16 8,12.7 3,16 4.5,10 0,6 6,5.5"/><polygon transform="translate(63 0)" points="8,0 10,5.5 16,6 11.5,10 13,16 8,12.7 3,16 4.5,10 0,6 6,5.5"/></g><polygon transform="translate(84 0)" points="8,0 10,5.5 16,6 11.5,10 13,16 8,12.7 3,16 4.5,10 0,6 6,5.5" fill="none" stroke="#f4c315" stroke-width="1.2"/></svg></div>
  </div>
  <div class="quote" style="left:444px;top:138px">
    <div class="avatar" role="img" aria-label="Client portrait"></div>
    <p>At vero eos et accusamus et iustodio dignissimos ducimus qui blanditiipraesent ium voluptatum deleniti atqu.</p>
    <div class="who">Tamsin R. Vale</div><div class="role">National Urban Fellow at the Houston</div>
    <div class="stars"><svg width="100" height="16" viewBox="0 0 100 16"><g fill="#f4c315"><polygon points="8,0 10,5.5 16,6 11.5,10 13,16 8,12.7 3,16 4.5,10 0,6 6,5.5"/><polygon transform="translate(21 0)" points="8,0 10,5.5 16,6 11.5,10 13,16 8,12.7 3,16 4.5,10 0,6 6,5.5"/><polygon transform="translate(42 0)" points="8,0 10,5.5 16,6 11.5,10 13,16 8,12.7 3,16 4.5,10 0,6 6,5.5"/><polygon transform="translate(63 0)" points="8,0 10,5.5 16,6 11.5,10 13,16 8,12.7 3,16 4.5,10 0,6 6,5.5"/><polygon transform="translate(84 0)" points="8,0 8,12.7 3,16 4.5,10 0,6 6,5.5"/></g><polygon transform="translate(84 0)" points="8,0 10,5.5 16,6 11.5,10 13,16 8,12.7 3,16 4.5,10 0,6 6,5.5" fill="none" stroke="#f4c315" stroke-width="1.2"/></svg></div>
  </div>
  <div class="quote" style="left:792px;top:138px">
    <div class="avatar" role="img" aria-label="Client portrait"></div>
    <p>At vero eos et accusamus et iustodio dignissimos ducimus qui blanditiipraesent ium voluptatum deleniti atqu.</p>
    <div class="who">Ruth Calder</div><div class="role">Creative Strategist | Entrepreneur &amp; Upcoming</div>
    <div class="stars"><svg width="100" height="16" viewBox="0 0 100 16"><g fill="#f4c315"><polygon points="8,0 10,5.5 16,6 11.5,10 13,16 8,12.7 3,16 4.5,10 0,6 6,5.5"/><polygon transform="translate(21 0)" points="8,0 10,5.5 16,6 11.5,10 13,16 8,12.7 3,16 4.5,10 0,6 6,5.5"/><polygon transform="translate(42 0)" points="8,0 10,5.5 16,6 11.5,10 13,16 8,12.7 3,16 4.5,10 0,6 6,5.5"/><polygon transform="translate(63 0)" points="8,0 10,5.5 16,6 11.5,10 13,16 8,12.7 3,16 4.5,10 0,6 6,5.5"/></g><polygon transform="translate(84 0)" points="8,0 10,5.5 16,6 11.5,10 13,16 8,12.7 3,16 4.5,10 0,6 6,5.5" fill="none" stroke="#f4c315" stroke-width="1.2"/></svg></div>
  </div>
</section>

<!-- partners -->
<h2 class="section-title" style="top:2642px">OUR STRATEGIC PARTNERS</h2>
<div class="abs partner" style="left:98px;top:2742px">Larkwen Finance</div>
<div class="abs partner" style="left:303px;top:2742px">hearthwyn</div>
<div class="abs partner" style="left:508px;top:2742px">lumbrel</div>
<div class="abs partner" style="left:713px;top:2742px">Brimvale Loans</div>
<div class="abs partner" style="left:918px;top:2742px">Quillan Loans</div>
<div class="abs partner" style="left:98px;top:2842px">Ninefern</div>
<div class="abs partner" style="left:303px;top:2842px">Corrowin Bank</div>
<div class="abs partner" style="left:508px;top:2842px">Tellwyn</div>
<div class="abs partner" style="left:713px;top:2842px">Orvel Direct</div>
<div class="abs partner" style="left:918px;top:2842px">Hollowmere Bank</div>

<!-- contact -->
<section class="abs contact">
  <h2 class="section-title">CONTACT US</h2>
  <h4 style="left:96px;top:153px">Contact form</h4>
  <div class="field" style="left:98px;top:216px;width:316px">Name :</div>
  <div class="field" style="left:420px;top:216px;width:308px">Phone no :</div>
  <div class="field" style="left:98px;top:262px;width:630px">Email :</div>
  <div class="field" style="left:98px;top:306px;width:630px;height:80px">Message :</div>
  <div class="submit">SUBMIT</div>

  <h4 style="left:782px;top:153px">Contact Information</h4>
  <div class="info" style="top:200px"><span class="ico"><svg width="12" height="16" viewBox="0 0 12 16"><path d="M6 0 a6 6 0 0 1 6 6 c0 4-6 10-6 10 S0 10 0 6 a6 6 0 0 1 6-6Z" fill="#fff"/><circle cx="6" cy="6" r="2.2" fill="#0e3672"/></svg></span><span>Shop 4B, 22 Alder St, Kenmore,<br>NSW 2190</span></div>
  <div class="info" style="top:256px;align-items:center"><span class="ico"><svg width="14" height="14" viewBox="0 0 14 14"><path d="M3 0 L5.5 3.5 L4 5.5 C5 8 6 9 8.5 10 L10.5 8.5 L14 11 L12 14 C5 13 1 9 0 2Z" fill="#fff"/></svg></span><span>1 800 555 0142</span></div>
  <div class="info" style="top:306px;align-items:center"><span class="ico"><svg width="15" height="11" viewBox="0 0 15 11"><rect x="0.5" y="0.5" width="14" height="10" fill="none" stroke="#fff"/><path d="M0.5 0.5 L7.5 6 L14.5 0.5" fill="none" stroke="#fff"/></svg></span><span>info@quantaraconsulting.com</span></div>
  <h4 style="left:782px;top:364px">Social Media</h4>
  <div class="social"><span>Gatherly</span><span>Chirpwell</span><span>Workloop</span><span>Pinbay</span></div>

  <div class="footer-rule"></div>
  <div class="copyright">Copyright © 2017, Quantara Consulting. All rights reserved.</div>
  <svg class="to-top" width="32" height="20" viewBox="0 0 32 20"><path d="M3 17 L16 4 L29 17" fill="none" stroke="#fff" stroke-width="3"/></svg>
</section>

</body>
</html>
```